LinkedIn Banner Design for B2B Consulting Firm

Take the already developed logo (attached) and incorporate it into a creative banner design for placement on LinkedIn (the social media platform targeting business users). The banner will be used on the firm's company profile page on LinkedIn (not yet created).

```html
<!DOCTYPE html>
<html lang="en">
<head>
<meta charset="utf-8">
<title>LinkedIn Banner Concepts – Fractional Marketing Services</title>
<link rel="stylesheet" href="https://fonts.googleapis.com/css2?family=Lato:wght@700;900&family=Source+Sans+3:wght@400&display=swap">
<style>
  :root {
    --board: #dcd8d8;
    --paper: #ffffff;
    --brand-green: #3f6848;
    --ink-grey: #4a4a4a;
    --warm-1: #a0553c;
    --warm-2: #d9b9a0;
    --dark-1: #3a3430;
    --dark-2: #b8946a;
    --cool-1: #9fb3c2;
    --cool-2: #e6ebee;
  }
  * { box-sizing: border-box; margin: 0; padding: 0; }
  html, body {
    width: 1200px;
    height: 797px;
    overflow: hidden;
    background: var(--board);
  }
  .board {
    position: relative;
    width: 1200px;
    height: 797px;
    background: var(--board);
  }
  .banner {
    position: absolute;
    left: 78px;
    width: 1043px;
    height: 176px;
    background: var(--paper);
    overflow: hidden;
    box-shadow: 0 1px 2px rgba(0,0,0,0.08);
  }
  .banner--one   { top: 112px; }
  .banner--two   { top: 311px; }
  .banner--three { top: 515px; }

  .banner__headline {
    position: absolute;
    left: 245px;
    top: 44px;
    font-family: "Lato", sans-serif;
    font-weight: 900;
    font-size: 28px;
    line-height: 32px;
    color: var(--brand-green);
    letter-spacing: 0.1px;
    white-space: nowrap;
  }
  .banner__audience {
    position: absolute;
    left: 245px;
    top: 119px;
    font-family: "Source Sans 3", sans-serif;
    font-size: 10.5px;
    color: var(--ink-grey);
    white-space: nowrap;
  }
  .banner--two .banner__audience { left: 247px; }

  .banner__brand {
    position: absolute;
    left: 500px;
    top: 122px;
    display: flex;
    align-items: center;
    gap: 7px;
    font-family: "Lato", sans-serif;
    font-weight: 700;
    font-size: 15px;
    color: var(--brand-green);
    white-space: nowrap;
  }
  .banner__brand-square {
    width: 12px;
    height: 12px;
    background: var(--brand-green);
  }
  .banner__photo {
    position: absolute;
    left: 0;
    top: 0;
    width: 1043px;
    height: 176px;
  }
</style>
</head>
<body>
<main class="board">

  <section class="banner banner--one">
    <svg class="banner__photo" viewBox="0 0 1043 176" role="img" aria-label="Photo of a smiling team gathered around a laptop in a brick-walled office">
      <defs>
        <linearGradient id="photo-warm" x1="0" y1="0" x2="1" y2="1">
          <stop offset="0" stop-color="var(--warm-1)"/>
          <stop offset="1" stop-color="var(--warm-2)"/>
        </linearGradient>
      </defs>
      <polygon points="656,0 1043,0 1043,176 832,176" fill="url(#photo-warm)"/>
    </svg>
    <h1 class="banner__headline">Fractional&nbsp; Marketing<br>Services to B2B clients</h1>
    <p class="banner__audience">Private Equity Firms, Family Offices, Investment Banks</p>
    <div class="banner__brand"><span class="banner__brand-square"></span>Northgate Advisory</div>
  </section>

  <section class="banner banner--two">
    <svg class="banner__photo" viewBox="0 0 1043 176" role="img" aria-label="Photo of colleagues laughing together around a desk in a plant-filled office">
      <defs>
        <linearGradient id="photo-dark" x1="0" y1="0" x2="1" y2="1">
          <stop offset="0" stop-color="var(--dark-1)"/>
          <stop offset="1" stop-color="var(--dark-2)"/>
        </linearGradient>
      </defs>
      <polygon points="666,0 1043,0 1043,176 842,176" fill="url(#photo-dark)"/>
    </svg>
    <h1 class="banner__headline">Fractional&nbsp; Marketing<br>Services to B2B clients</h1>
    <p class="banner__audience">Private Equity Firms, Family Offices, Investment Banks</p>
    <div class="banner__brand"><span class="banner__brand-square"></span>Northgate Advisory</div>
  </section>

  <section class="banner banner--three">
    <svg class="banner__photo" viewBox="0 0 1043 176" role="img" aria-label="Photo of a diverse team meeting around a laptop in a bright office">
      <defs>
        <linearGradient id="photo-cool" x1="0" y1="0" x2="1" y2="1">
          <stop offset="0" stop-color="var(--cool-1)"/>
          <stop offset="1" stop-color="var(--cool-2)"/>
        </linearGradient>
      </defs>
      <polygon points="656,0 1043,0 1043,176 832,176" fill="url(#photo-cool)"/>
    </svg>
    <h1 class="banner__headline">Fractional&nbsp; Marketing<br>Services to B2B clients</h1>
    <p class="banner__audience">Private Equity Firms, Family Offices, Investment Banks</p>
    <div class="banner__brand"><span class="banner__brand-square"></span>Northgate Advisory</div>
  </section>

</main>
</body>
</html>
```